BOLD & MINIMALIST DESIGN NEEDED

We want a very bold but minimalistic business card design that is impactful and utilizes both sides of the business card. Our current logo is included for your use.

We want bold fonts and good use of negative space. We don't want the logo to overpower the design.

Target Market(s)

Professionals who are building new commercial buildings.

Industry/Entity Type

Construction

Contact Information for Business Card

Name, Title, email, office phone, cell phone, website

Font styles to use
Serif
Sans Serif

Requirements
Must have
• Bold design!

```html
<!DOCTYPE html>
<html lang="en">
<head>
<meta charset="utf-8">
<title>Ridgeway Design + Build — Business Card</title>
<link href="https://fonts.googleapis.com/css2?family=Montserrat:wght@400;500;800&display=swap" rel="stylesheet">
<style>
  :root {
    --backdrop: #3b3b3b;
    --card-white: #ffffff;
    --card-black: #1c1c1c;
    --brand-green: #5b9a2e;
    --brand-green-bright: #7cc544;
    --ink: #2a2a2a;
    --ink-soft: #555555;
  }
  * { box-sizing: border-box; margin: 0; padding: 0; }
  html, body {
    width: 1200px; height: 791px; overflow: hidden;
    background: var(--backdrop);
    font-family: "Montserrat", sans-serif;
  }
  .stage {
    position: relative; width: 1200px; height: 791px;
    display: flex; align-items: center; justify-content: center; gap: 50px;
  }
  .card {
    position: relative; width: 525px; height: 300px;
    border-bottom: 3px solid var(--brand-green);
  }
  .card--front { background: var(--card-white); }
  .card--back {
    background: var(--card-black);
    display: flex; align-items: center; justify-content: center;
  }
  .person {
    position: absolute; right: 40px; top: 62px; text-align: right;
  }
  .person__name {
    font-weight: 800; font-size: 22px; color: var(--brand-green);
    letter-spacing: 0.5px;
  }
  .person__title {
    font-size: 14px; color: var(--ink-soft); margin-top: 2px;
  }
  .divider {
    position: absolute; left: 32px; right: 22px; top: 190px;
    height: 1px; background: var(--brand-green);
  }
  .brand-name {
    position: absolute; left: 36px; top: 128px;
    display: flex; align-items: center; gap: 10px;
    font-weight: 800; font-size: 24px; color: var(--ink);
    letter-spacing: 0.5px;
  }
  .brand-name__mark {
    width: 16px; height: 16px; background: var(--brand-green);
  }
  .contact {
    position: absolute; left: 36px; top: 202px; list-style: none;
  }
  .contact__item {
    display: flex; align-items: center; gap: 8px;
    font-size: 13px; color: var(--ink-soft); line-height: 20px;
  }
  .contact__icon { width: 11px; height: 11px; flex: none; }
  .back-brand {
    display: flex; align-items: center; gap: 12px;
    font-weight: 800; font-size: 30px; color: var(--brand-green-bright);
    letter-spacing: 1px;
  }
  .back-brand__mark {
    width: 18px; height: 18px; background: var(--brand-green-bright);
  }
</style>
</head>
<body>
<main class="stage">
  <section class="card card--front" aria-label="Card front">
    <div class="person">
      <p class="person__name">MARTIN CORWELL</p>
      <p class="person__title">President</p>
    </div>
    <div class="brand-name">
      <span class="brand-name__mark"></span>
      <span>RIDGEWAY DESIGN + BUILD</span>
    </div>
    <div class="divider"></div>
    <ul class="contact">
      <li class="contact__item">
        <svg class="contact__icon" viewBox="0 0 12 12"><path d="M2 1h3l1 3-2 1a7 7 0 0 0 3 3l1-2 3 1v3c-6 0-10-4-9-9z" fill="#5b9a2e"/></svg>
        555-014-3380
      </li>
      <li class="contact__item">
        <svg class="contact__icon" viewBox="0 0 12 12"><rect x="3" y="0.5" width="6" height="11" rx="1" fill="none" stroke="#5b9a2e" stroke-width="1.2"/></svg>
        555-014-3380
      </li>
      <li class="contact__item">
        <svg class="contact__icon" viewBox="0 0 12 12"><rect x="0.5" y="2" width="11" height="8" fill="#5b9a2e"/><path d="M0.5 2l5.5 4 5.5-4" fill="none" stroke="#fff" stroke-width="1"/></svg>
        m.corwell@rdb-build.com
      </li>
      <li class="contact__item">
        <svg class="contact__icon" viewBox="0 0 12 12"><circle cx="6" cy="6" r="5.5" fill="#5b9a2e"/><path d="M0.5 6h11M6 0.5c-3 3-3 8 0 11M6 0.5c3 3 3 8 0 11" fill="none" stroke="#fff" stroke-width="0.8"/></svg>
        www.rdb-build.com
      </li>
    </ul>
  </section>

  <section class="card card--back" aria-label="Card back">
    <div class="back-brand">
      <span class="back-brand__mark"></span>
      <span>RIDGEWAY</span>
    </div>
  </section>
</main>
</body>
</html>
```